Business card for Crestline Bathrooms

Please design a business card for our bathroom renovation business. You can use my existing logo, but if you have an idea to modernize it, I would like to see it. Please see attached files first. I would like to use the blue and the orange theme. I like the concept of using the shower head in the logo. Please find following a design (or two) that I have been trying to create with my limited resources. That design was for a sign, but I was going to adopt it and use it as a business card as well. I like the concept of the water splash but I don’t think it “flows” nicely together with the logo. Another thought is that maybe creating the logo out of water splash could work and have a dramatic effect (like the water text and the butterfly picture attached with similar background instead of white). If the above doesn’t work I would like to see a modern simplified design. One of the attached files named as the unwanted business card has all the details that I want included in the business card. Please note that it is two sided.
Updates

I am very thankful for the designs that I have received, but they are very similar and only a couple of attempts to do something with the water splash as per my original brief. Modernizing the logo and having it made out of out of water splash with the orange as color accent could work and have a dramatic effect (like the water text and the butterfly picture attached with similar background instead of white). Please do not use the butterfly itself! This is just an example that images can be created out of water splash.

Contact Information for Business Card

all the details are on the unwonted business card file included

Colors
3176b5

Requirements
Nice to have
• Copied from the brief:
• ... maybe creating the logo out of water splash could work and have a dramatic effect (like the water text and the butterfly picture attached with similar background instead of white). Please do not use the butterfly itself!
Should not have
• I am getting designs with a butterfly. The butterfly picture was an example of creating something from a water splash. The butterfly itself has no association with anything other than the concept of creating a logo out of water splash. Sorry, I thought I was clear in the brief.

```html
<!DOCTYPE html>
<html lang="en">
<head>
<meta charset="utf-8">
<title>Crestline Bathrooms – Business Card</title>
<link href="https://fonts.googleapis.com/css2?family=Roboto:ital,wght@0,500;0,700;1,700&family=Roboto+Condensed:wght@500;700&display=swap" rel="stylesheet">
<style>
  :root {
    --backdrop: #34464f;
    --card-top: #3f72b8;
    --card-bottom: #6e90c8;
    --splash-deep: #2f5f9e;
    --splash-light: #8fb0dc;
    --ink: #14203a;
    --text-light: #d6e3f5;
    --rule: #0f1a30;
  }
  * { box-sizing: border-box; margin: 0; padding: 0; }
  html, body { width: 1200px; height: 1200px; overflow: hidden; }
  body {
    background: var(--backdrop);
    font-family: "Roboto", Arial, sans-serif;
    position: relative;
  }
  .card {
    position: absolute;
    left: 170px;
    width: 860px;
    height: 500px;
    background: linear-gradient(180deg, var(--card-top), var(--card-bottom));
    box-shadow: 0 14px 30px rgba(0,0,0,.35);
    overflow: hidden;
  }
  .card--back { top: 60px; }
  .card--front { top: 640px; }
  .splash {
    position: absolute;
    inset: 0;
    background:
      radial-gradient(ellipse 45% 55% at 60% 70%, rgba(143,176,220,.45), transparent 70%),
      radial-gradient(ellipse 35% 40% at 30% 30%, rgba(47,95,158,.35), transparent 70%);
  }
  .brand {
    position: absolute;
    font-family: "Roboto", Arial, sans-serif;
    font-weight: 700;
    color: var(--text-light);
    line-height: 1;
    text-align: center;
  }
  .card--back .brand {
    top: 50px; left: 0; right: 0;
    font-size: 58px;
  }
  .embossed {
    color: var(--ink);
    text-shadow: 0 1px 0 rgba(214,227,245,.55);
  }
  .services-band {
    position: absolute;
    top: 150px; left: 0; right: 0;
    height: 50px;
    border-top: 5px double var(--rule);
    border-bottom: 5px double var(--rule);
    display: flex; align-items: center; justify-content: center;
  }
  .services-band h2 {
    font-size: 20px; font-weight: 700; letter-spacing: 1px;
    color: var(--text-light);
    text-shadow: 0 1px 1px var(--rule);
  }
  .services-list {
    position: absolute;
    top: 222px; left: 90px; right: 40px;
    list-style: none;
    font-style: italic;
    font-weight: 700;
    font-size: 22px;
    letter-spacing: 1px;
    line-height: 1.45;
    white-space: nowrap;
  }
  .card--front .brand {
    top: 180px; left: 40px; width: 400px;
    font-size: 52px;
  }
  .divider {
    position: absolute;
    left: 450px; top: 40px;
    width: 14px; height: 400px;
    background: var(--splash-light);
    border: 3px solid var(--rule);
  }
  .contact {
    position: absolute;
    left: 490px; top: 110px;
    width: 345px;
  }
  .contact .name {
    font-family: "Roboto Condensed", Arial, sans-serif;
    font-weight: 700;
    font-size: 36px;
    padding-bottom: 6px;
    border-bottom: 3px solid var(--rule);
    margin-bottom: 26px;
    white-space: nowrap;
  }
  .row {
    display: flex; align-items: center; gap: 14px;
    margin-bottom: 16px;
  }
  .row svg { flex: none; }
  .row p {
    font-weight: 700; font-size: 22px; line-height: 1.3;
    white-space: nowrap;
  }
  .row p.big { font-size: 26px; letter-spacing: 1px; }
  .row p.web { font-family: "Roboto Condensed", Arial, sans-serif; font-size: 20px; }
</style>
</head>
<body>

<section class="card card--back">
  <div class="splash" role="img" aria-label="Blue water splash photograph"></div>
  <div class="brand">Crestline Bathrooms</div>
  <div class="services-band"><h2>SERVICES</h2></div>
  <ul class="services-list embossed">
    <li>&gt; COMPLETE BATHROOM RENOVATIONS &amp; REMODELLING</li>
    <li>&gt; HIGHLY SKILLED &amp; QUALIFIED TRADESPEOPLE</li>
    <li>&gt; PROFESSIONAL SERVICE FROM CONCEPT TO COMPLETION</li>
    <li>&gt; ALL WORK GUARANTEED</li>
  </ul>
</section>

<section class="card card--front">
  <div class="splash" role="img" aria-label="Blue water splash photograph"></div>
  <div class="brand">Crestline Bathrooms</div>
  <div class="divider"></div>
  <div class="contact">
    <div class="name embossed">MARCUS DELANEY</div>
    <div class="row">
      <svg width="40" height="44" viewBox="0 0 40 44" aria-hidden="true">
        <polygon points="20,2 38,12 38,32 20,42 2,32 2,12" fill="#0f1a30"/>
        <text x="20" y="29" text-anchor="middle" font-family="Roboto, sans-serif" font-weight="700" font-size="18" fill="#fff">A</text>
      </svg>
      <p class="embossed">PO Box 41<br>Harwood Vale 2734</p>
    </div>
    <div class="row">
      <svg width="40" height="44" viewBox="0 0 40 44" aria-hidden="true">
        <polygon points="20,2 38,12 38,32 20,42 2,32 2,12" fill="#0f1a30"/>
        <text x="20" y="29" text-anchor="middle" font-family="Roboto, sans-serif" font-weight="700" font-size="18" fill="#fff">P</text>
      </svg>
      <p class="embossed big">0400 555 218<br>5550 1847</p>
    </div>
    <div class="row">
      <svg width="40" height="44" viewBox="0 0 40 44" aria-hidden="true">
        <polygon points="20,2 38,12 38,32 20,42 2,32 2,12" fill="#0f1a30"/>
        <text x="20" y="29" text-anchor="middle" font-family="Roboto, sans-serif" font-weight="700" font-size="18" fill="#fff">W</text>
      </svg>
      <p class="embossed web">marcus@crestlinebathrooms.com.au<br>crestlinebathrooms.com.au</p>
    </div>
  </div>
</section>

</body>
</html>
```